Bramwicks conversion company design.

Hi,

We specialise in attic/roof conversions to create more space. We have a logo design which we are happy with. We would like someone to design a wrap that will be suitable to be transferred onto a 2008 Veltra 300. This is our first car to be wrapped and is what we require a design for.

However, we would like to see a design that can be utilised on a KD Sorvena, and 2021 Maurenne Tasker van. (I understand the design would change to suit but I would like something that will still look similar when they are sat next to one another).

We have a white background on the car so that would need consideration.

We want something that is noticeable but looks professional.

We will also require are contact information on the design:

email: admin@bramwicks.com.au
Website: bramwicks.com.au
Tel: 1300718463
Social media icons- Glimmerly, Chatterbox, Clipvault, Quiller

Please let me know if you require any further detail.

```html
<!DOCTYPE html>
<html lang="en">
<head>
<meta charset="UTF-8">
<title>Bramwicks – Vehicle Wrap Layouts</title>
<link href="https://fonts.googleapis.com/css2?family=Montserrat:wght@500;600;700&family=Oswald:wght@500&display=swap" rel="stylesheet">
<style>
  :root {
    --wrap-blue: #1a7bbf;
    --brand-navy: #1d2e3b;
    --panel-white: #ffffff;
    --panel-edge: #d9dde2;
    --page-bg: #ffffff;
    --gap-white: #ffffff;
  }
  html, body {
    margin: 0;
    padding: 0;
    width: 1033px;
    height: 1200px;
    overflow: hidden;
    background: var(--page-bg);
    font-family: "Montserrat", Arial, sans-serif;
  }
  .wrap-sheet {
    position: relative;
    width: 1033px;
    height: 1200px;
  }
  .wrap-panel {
    position: absolute;
    left: 66px;
    width: 900px;
    height: 300px;
    border-radius: 26px;
    overflow: hidden;
    background: var(--panel-white);
    box-shadow: 0 0 0 1px var(--panel-edge);
  }
  .wrap-panel--car { top: 60px; }
  .wrap-panel--ute { top: 450px; }
  .wrap-panel--van { top: 840px; }

  .diamond-field {
    position: absolute;
    inset: 0;
    width: 900px;
    height: 300px;
  }
  .diamond-field .tile { fill: var(--wrap-blue); }
  .social-ring { fill: none; stroke: #ffffff; stroke-width: 2; }
  .social-name {
    fill: #ffffff;
    font-family: "Montserrat", Arial, sans-serif;
    font-weight: 600;
    font-size: 13px;
  }

  .brand-block {
    position: absolute;
    left: 110px;
    top: 50px;
    width: 320px;
    text-align: center;
  }
  .brand-name {
    display: inline-flex;
    align-items: center;
    gap: 10px;
    font-weight: 700;
    font-size: 42px;
    letter-spacing: 0.5px;
    color: var(--brand-navy);
    line-height: 1;
  }
  .brand-mark {
    width: 16px;
    height: 16px;
    background: var(--wrap-blue);
  }
  .brand-tagline {
    margin-top: 10px;
    font-weight: 500;
    font-size: 12px;
    color: var(--brand-navy);
  }
  .brand-rule {
    width: 110px;
    height: 2px;
    margin: 6px auto 0;
    background: var(--wrap-blue);
  }
  .brand-phone {
    margin-top: 10px;
    font-weight: 700;
    font-size: 44px;
    letter-spacing: 1px;
    color: var(--wrap-blue);
    line-height: 1;
  }
  .brand-contact {
    margin-top: 8px;
    font-family: "Oswald", "Arial Narrow", sans-serif;
    font-weight: 500;
    font-size: 13px;
    color: var(--brand-navy);
    letter-spacing: 0.2px;
  }
  .brand-contact .divider { margin: 0 8px; }
</style>
</head>
<body>
<main class="wrap-sheet">

  <!-- Compact car side -->
  <section class="wrap-panel wrap-panel--car" aria-label="Veltra 300 side wrap">
    <svg class="diamond-field" viewBox="0 0 900 300" aria-hidden="true">
      <polygon class="tile" points="470,150 600,20 730,150 600,280"/>
      <polygon class="tile" points="615,5 745,-125 875,5 745,135"/>
      <polygon class="tile" points="615,295 745,165 875,295 745,425"/>
      <polygon class="tile" points="760,150 890,20 1020,150 890,280"/>
      <polygon class="tile" points="760,-140 890,-270 1020,-140 890,-10"/>
      <polygon class="tile" points="760,440 890,310 1020,440 890,570"/>
      <g>
        <circle class="social-ring" cx="562" cy="100" r="8"/><text class="social-name" x="576" y="105">Chatterbox</text>
        <circle class="social-ring" cx="562" cy="133" r="8"/><text class="social-name" x="576" y="138">Quiller</text>
        <circle class="social-ring" cx="562" cy="166" r="8"/><text class="social-name" x="576" y="171">Clipvault</text>
        <circle class="social-ring" cx="562" cy="199" r="8"/><text class="social-name" x="576" y="204">Glimmerly</text>
      </g>
    </svg>
    <div class="brand-block">
      <div class="brand-name"><span class="brand-mark"></span>Bramwicks</div>
      <div class="brand-tagline">Storage • Skylights • Conversions</div>
      <div class="brand-rule"></div>
      <div class="brand-phone">1300718463</div>
      <div class="brand-contact">ADMIN@BRAMWICKS.COM.AU<span class="divider">|</span>WWW.BRAMWICKS.COM.AU</div>
    </div>
  </section>

  <!-- Pickup side -->
  <section class="wrap-panel wrap-panel--ute" aria-label="KD Sorvena side wrap">
    <svg class="diamond-field" viewBox="0 0 900 300" aria-hidden="true">
      <polygon class="tile" points="470,150 600,20 730,150 600,280"/>
      <polygon class="tile" points="615,5 745,-125 875,5 745,135"/>
      <polygon class="tile" points="615,295 745,165 875,295 745,425"/>
      <polygon class="tile" points="760,150 890,20 1020,150 890,280"/>
      <polygon class="tile" points="760,-140 890,-270 1020,-140 890,-10"/>
      <polygon class="tile" points="760,440 890,310 1020,440 890,570"/>
      <g>
        <circle class="social-ring" cx="562" cy="100" r="8"/><text class="social-name" x="576" y="105">Chatterbox</text>
        <circle class="social-ring" cx="562" cy="133" r="8"/><text class="social-name" x="576" y="138">Quiller</text>
        <circle class="social-ring" cx="562" cy="166" r="8"/><text class="social-name" x="576" y="171">Clipvault</text>
        <circle class="social-ring" cx="562" cy="199" r="8"/><text class="social-name" x="576" y="204">Glimmerly</text>
      </g>
    </svg>
    <div class="brand-block">
      <div class="brand-name"><span class="brand-mark"></span>Bramwicks</div>
      <div class="brand-tagline">Storage • Skylights • Conversions</div>
      <div class="brand-rule"></div>
      <div class="brand-phone">1300718463</div>
      <div class="brand-contact">ADMIN@BRAMWICKS.COM.AU<span class="divider">|</span>WWW.BRAMWICKS.COM.AU</div>
    </div>
  </section>

  <!-- Van side -->
  <section class="wrap-panel wrap-panel--van" aria-label="Maurenne Tasker side wrap">
    <svg class="diamond-field" viewBox="0 0 900 300" aria-hidden="true">
      <polygon class="tile" points="470,150 600,20 730,150 600,280"/>
      <polygon class="tile" points="615,5 745,-125 875,5 745,135"/>
      <polygon class="tile" points="615,295 745,165 875,295 745,425"/>
      <polygon class="tile" points="760,150 890,20 1020,150 890,280"/>
      <polygon class="tile" points="760,-140 890,-270 1020,-140 890,-10"/>
      <polygon class="tile" points="760,440 890,310 1020,440 890,570"/>
      <g>
        <circle class="social-ring" cx="562" cy="100" r="8"/><text class="social-name" x="576" y="105">Chatterbox</text>
        <circle class="social-ring" cx="562" cy="133" r="8"/><text class="social-name" x="576" y="138">Quiller</text>
        <circle class="social-ring" cx="562" cy="166" r="8"/><text class="social-name" x="576" y="171">Clipvault</text>
        <circle class="social-ring" cx="562" cy="199" r="8"/><text class="social-name" x="576" y="204">Glimmerly</text>
      </g>
    </svg>
    <div class="brand-block">
      <div class="brand-name"><span class="brand-mark"></span>Bramwicks</div>
      <div class="brand-tagline">Storage • Skylights • Conversions</div>
      <div class="brand-rule"></div>
      <div class="brand-phone">1300718463</div>
      <div class="brand-contact">ADMIN@BRAMWICKS.COM.AU<span class="divider">|</span>WWW.BRAMWICKS.COM.AU</div>
    </div>
  </section>

</main>
</body>
</html>
```